Fresh Dwelling Tract Guide needs a new Landing Page

I like to get a landing page or website with 2-3 pages to help target home buyers who are looking to buy homes from builders such as TW Residences, Morvik, P.L. Fennick, etc. The landing page/website to be non-cluttered and be able to explain to home buyers that there are many benefits to include me as their buyer's agent when they buy a brand new home from any builders.
I may want to incorporate a short explanation video (animated) on the landing page and then for the viewer to click on a button that will take them to another page where they can search for new homes from different builders.
Target Market(s)
Home buyers looking to buy brand new home from builders such as TW Residences, Morvik, P.L. Fennick, etc.
Industry/Entity Type
Real Estate
Number of Pages Required
2 page
Font styles to use
Requirements
Must have
- The landing page may have the explanation video at the bottom of the landing page (scrolled down) or there may be a CALL TO ACTION button that takes the viewer to the 2nd page to watch the explanation video. Once they watched the explanation video and are still interested, they can click on another CALL TO ACTION button that will take them to another website that they will be able to search for all the available new homes and register their contact information.
Should not have
- No clutters and no dark colors.

```html
<!DOCTYPE html>
<html lang="en">
<head>
<meta charset="utf-8">
<title>Fresh Dwelling Tract Guide – Contact</title>
<link rel="stylesheet" href="https://fonts.googleapis.com/css2?family=Lora:wght@400&family=Open+Sans:wght@400;600;700&display=swap">
<style>
  :root {
    --bg: #ffffff;
    --olive: #a9b944;
    --brown: #5b4a37;
    --text: #4e4536;
    --placeholder: #b4aca0;
    --link: #3a8ad8;
    --rule: #f1efec;
    --field-shadow: rgba(0, 0, 0, 0.06);
  }
  * { box-sizing: border-box; margin: 0; padding: 0; }
  html, body { width: 1200px; height: 1200px; overflow: hidden; background: var(--bg); }
  body { position: relative; font-family: "Open Sans", sans-serif; color: var(--text); }

  .field {
    position: absolute;
    background: var(--bg);
    box-shadow: 0 2px 8px var(--field-shadow);
    font-size: 12.5px;
    font-weight: 600;
    letter-spacing: 1.3px;
    color: var(--placeholder);
    padding-left: 28px;
  }
  .field--phone { left: 88px; top: 8px; width: 430px; height: 54px; line-height: 54px; }
  .field--comments { left: 88px; top: 94px; width: 430px; height: 178px; padding-top: 19px; padding-left: 31px; }
  .field--email { left: 691px; top: 720px; width: 421px; height: 54px; line-height: 54px; }

  .button {
    position: absolute;
    background: var(--olive);
    color: #fff;
    border-radius: 2px;
    font-weight: 700;
    font-size: 14.5px;
    letter-spacing: 2px;
    text-align: center;
  }
  .button--submit { left: 88px; top: 374px; width: 430px; height: 55px; line-height: 55px; }
  .button--signup { left: 691px; top: 812px; width: 163px; height: 54px; line-height: 54px; }

  .footer-rule { position: absolute; left: 0; top: 558px; width: 1200px; height: 1px; background: var(--rule); }
  .page-end { position: absolute; left: 0; top: 1198px; width: 1200px; height: 1px; background: var(--rule); }

  .footer-divider { position: absolute; left: 600px; top: 640px; width: 1px; height: 408px; background: var(--brown); }

  .footer-title {
    position: absolute;
    font-family: "Lora", serif;
    font-weight: 400;
    font-size: 23px;
    color: var(--brown);
    top: 654px;
  }
  .footer-title--about { left: 88px; }
  .footer-title--updates { left: 691px; }

  .about-text { position: absolute; left: 88px; top: 719px; width: 420px; font-size: 15px; line-height: 20.6px; }
  .about-text p + p { margin-top: 26px; }

  .email-link { position: absolute; left: 88px; top: 937px; font-size: 15px; color: var(--link); text-decoration: none; }

  .brand { position: absolute; left: 88px; top: 1034px; display: flex; align-items: center; gap: 10px; }
  .brand__dot { width: 14px; height: 14px; border-radius: 50%; background: var(--olive); }
  .brand__name { font-size: 22px; font-weight: 400; color: var(--brown); }
</style>
</head>
<body>
  <section class="contact-form">
    <div class="field field--phone">Phone Number</div>
    <div class="field field--comments">Questions/Comments</div>
    <div class="button button--submit">SUBMIT</div>
  </section>

  <div class="footer-rule"></div>

  <footer class="site-footer">
    <h2 class="footer-title footer-title--about">ABOUT US</h2>
    <div class="about-text">
      <p>Lorem ipsum dolor sit amet, consectetur adipisicing elit, sed do eiusmod incididunt ut labore et dolore magna aliqua. Ut enim ad minim veniam,</p>
      <p>Lorem ipsum dolor sit amet, consectetur adipisicing elit, sed do eiusmod tempor incididunt ut labore et dolore magna aliqua. Ut enim ad minim veniam, quis nostrud exercitation ullamco laboris nisi ut aliquip ex ea commodo consequat.</p>
    </div>
    <a class="email-link" href="#">Email us</a>
    <div class="brand">
      <span class="brand__dot"></span>
      <span class="brand__name">Parkside House Walk</span>
    </div>

    <div class="footer-divider"></div>

    <h2 class="footer-title footer-title--updates">GET UPDATES</h2>
    <div class="field field--email">Your Email</div>
    <div class="button button--signup">SIGN UP</div>
  </footer>

  <div class="page-end"></div>
</body>
</html>
```